Coastline Premier Retreats Business Card Design

Design a business card for Coastline Premier Retreats. Look at the website for colors and reference. Card should have logo, name, title, office number, mobile number, email, URL and a tagline like, "Luxury Hotel & Resort Email Marketing" (This might change).

https://www.coastlinepremierretreats.example

The rest I will leave up to your imagination.

Contact Information for Business Card

Logo, name, title, office number, mobile number, email, URL and a tagline like, "Luxury Hotel & Resort Email Marketing" (This might change).

```html
<!DOCTYPE html>
<html lang="en">
<head>
<meta charset="utf-8">
<title>Coastline Premier Retreats – Business Card</title>
<link rel="stylesheet" href="https://fonts.googleapis.com/css2?family=Montserrat:wght@400;500;700;800&display=swap">
<style>
  :root {
    --bg: #d9d9d9;
    --card-dark: #0d0d0d;
    --card-dark-2: #2a2a2a;
    --card-light: #f4f4f4;
    --orange: #e8782a;
    --ink: #1a1a1a;
    --white: #ffffff;
  }
  * { box-sizing: border-box; margin: 0; padding: 0; }
  html, body { width: 1200px; height: 1200px; overflow: hidden; }
  body {
    background: var(--bg);
    font-family: "Montserrat", sans-serif;
    color: var(--ink);
    position: relative;
  }
  .card {
    position: absolute;
    left: 150px;
    width: 900px;
    height: 515px;
    border-radius: 28px;
    overflow: hidden;
    box-shadow: 0 6px 18px rgba(0,0,0,0.18);
  }
  /* Front */
  .card-front {
    top: 60px;
    background: var(--card-dark);
  }
  .front-texture {
    position: absolute; inset: 0;
    background: linear-gradient(135deg, var(--card-dark-2) 0%, #161616 45%, var(--card-dark) 100%);
  }
  .front-brand {
    position: absolute;
    left: 50%; top: 50%;
    transform: translate(-50%, -50%);
    display: flex; align-items: center; gap: 18px;
    white-space: nowrap;
  }
  .brand-square {
    width: 26px; height: 26px;
    background: var(--orange);
    flex: none;
  }
  .front-brand .brand-name {
    font-weight: 800;
    font-size: 44px;
    letter-spacing: 1px;
    color: var(--white);
    text-transform: uppercase;
  }
  /* Back */
  .card-back {
    top: 625px;
    background: var(--card-light);
  }
  .back-brand {
    position: absolute;
    left: 60px; top: 210px;
    width: 300px;
    display: flex; align-items: center; gap: 12px;
  }
  .back-brand .brand-square { width: 18px; height: 18px; }
  .back-brand .brand-name {
    font-weight: 800;
    font-size: 25px;
    line-height: 1.15;
    color: var(--ink);
    text-transform: uppercase;
  }
  .divider {
    position: absolute;
    left: 390px; top: 70px;
    width: 2px; height: 300px;
    background: var(--ink);
  }
  .details {
    position: absolute;
    left: 420px; top: 62px;
    width: 460px;
  }
  .person-name {
    font-weight: 800;
    font-size: 34px;
    color: var(--orange);
    line-height: 1.1;
  }
  .person-title {
    font-size: 18px;
    font-weight: 500;
    margin-top: 4px;
  }
  .address {
    font-size: 17px;
    font-weight: 500;
    line-height: 1.35;
    margin-top: 16px;
  }
  .contact-list {
    list-style: none;
    margin-top: 16px;
    font-size: 17px;
    font-weight: 500;
  }
  .contact-list li {
    display: flex; align-items: center; gap: 12px;
    line-height: 1.6;
    white-space: nowrap;
  }
  .contact-list svg { width: 16px; height: 16px; flex: none; }
  .tagline {
    position: absolute;
    left: 0; right: 0; bottom: 50px;
    text-align: center;
    padding-left: 200px;
    font-size: 20px;
    font-weight: 500;
    color: var(--orange);
  }
</style>
</head>
<body>

  <section class="card card-front" aria-label="Card front">
    <div class="front-texture" role="img" aria-label="Dark background with a faint repeating tonal pattern"></div>
    <div class="front-brand">
      <span class="brand-square"></span>
      <span class="brand-name">Coastline Premier Retreats</span>
    </div>
  </section>

  <section class="card card-back" aria-label="Card back">
    <div class="back-brand">
      <span class="brand-square"></span>
      <span class="brand-name">Coastline Premier Retreats</span>
    </div>

    <div class="divider"></div>

    <div class="details">
      <h1 class="person-name">Daniel Mercer</h1>
      <p class="person-title">Founder &amp; Director</p>
      <p class="address">North America, 4180 Harbor View Road<br>Port Ellis Maine 04512</p>
      <ul class="contact-list">
        <li>
          <svg viewBox="0 0 24 24" fill="var(--orange)"><path d="M6.6 10.8a15.1 15.1 0 0 0 6.6 6.6l2.2-2.2c.3-.3.7-.4 1-.2 1.1.4 2.3.6 3.6.6.6 0 1 .4 1 1V20c0 .6-.4 1-1 1A17 17 0 0 1 3 4c0-.6.4-1 1-1h3.5c.6 0 1 .4 1 1 0 1.3.2 2.5.6 3.6.1.3 0 .7-.2 1z"/></svg>
          555.214.6000
        </li>
        <li>
          <svg viewBox="0 0 24 24" fill="none" stroke="var(--orange)" stroke-width="2.2"><rect x="6" y="2" width="12" height="20" rx="2"/><line x1="11" y1="18" x2="13" y2="18"/></svg>
          555-487-3921
        </li>
        <li>
          <svg viewBox="0 0 24 24" fill="var(--orange)"><path d="M2 5h20v14H2z"/><path d="M2 5l10 8 10-8" fill="none" stroke="var(--card-light)" stroke-width="1.8"/></svg>
          info@coastlinepremierretreats.example
        </li>
        <li>
          <svg viewBox="0 0 24 24" fill="none" stroke="var(--orange)" stroke-width="2.2"><circle cx="12" cy="12" r="9.5"/><path d="M2.5 12h19M12 2.5c3 3 3 16 0 19M12 2.5c-3 3-3 16 0 19"/></svg>
          www.coastlinepremierretreats.example
        </li>
      </ul>
    </div>

    <p class="tagline">Luxury Hotel &amp; Resort Email Marketing</p>
  </section>

</body>
</html>
```